Wordpress Design Project for Bankruptcy Law Office in San Francisco

our current website: www.dorvanelilaw-example.com

we would like to re-design it for wordpress to make it faster and a bit more modern.

content should be similar to what we have there right now but also we do family law

please include logo for law office:

Law Office of Marta K. Dolvenidze

Thank you.
Updates

please see attached word document with logos that we like as an example.

we do tend to like color red.  darker red.

Please submit your design variations and logo as soon as possible.   We would like to go over them and make our decision

Reason: Please create couple of more variations of logo for your design, so we can make our decision what we like the most. Please see word doc for samples: Text: Law Office Of Marta K. Dolvenidze

Reason: final touches

Target Market(s)

bankruptcy and family law clients

Industry/Entity Type

Family Law

Requirements
Must have
• see examples of law sites
http://promo.lexorbin-example.com/testimonials

- new logo: Law Office of Marta K. Dolvenidze
- client intake form
- blog
- contact us form

Nice to have
• - map
- red color
- on the front page a nice photo of SF or a happy family

```html
<!DOCTYPE html>
<html lang="en">
<head>
<meta charset="utf-8">
<title>Law Office of Marta K. Dolvenidze</title>
<link href="https://fonts.googleapis.com/css2?family=Cabin:ital,wght@0,400;0,500;1,400&family=Crimson+Text&family=Open+Sans:wght@400;600&display=swap" rel="stylesheet">
<style>
:root{
  --red:#c4161c;
  --red-dark:#9b0b0f;
  --red-deep:#8c0a0d;
  --page:#f2f2f2;
  --white:#ffffff;
  --text:#4a4a4a;
  --grey:#777;
  --dots:#b5b5b5;
  --gold:#f2c200;
}
*{margin:0;padding:0;box-sizing:border-box}
html,body{width:957px;height:1200px;overflow:hidden}
body{background:var(--page);font-family:"Open Sans",sans-serif;color:var(--text);position:relative}
.abs{position:absolute}
.top-bar{left:0;top:0;width:957px;height:5px;background:var(--red)}
.logo-mark{left:61px;top:24px;width:60px;height:60px;border-radius:50%;background:radial-gradient(circle at 40% 35%,#e0343a,var(--red-dark));box-shadow:0 1px 3px rgba(0,0,0,.3)}
.logo-name{left:132px;top:26px;font-family:"Crimson Text",serif;line-height:1}
.logo-name .l1{font-size:28px;letter-spacing:.5px;display:block;color:var(--red)}
.logo-name .l2{font-size:18px;letter-spacing:.6px;display:block;margin-top:8px;color:var(--grey)}
.search{left:741px;top:43px;width:157px;height:22px;border:1px solid #ccc;background:var(--white);border-radius:2px;font-size:9px;font-style:italic;color:#aaa;padding:4px 12px}
.search svg{position:absolute;right:5px;top:5px}
.nav-band{left:0;top:110px;width:957px;height:24px;background:var(--red)}
.nav{left:59px;top:100px;width:841px;height:42px;display:flex;background:linear-gradient(var(--red),var(--red-dark));border-radius:3px 3px 0 0;box-shadow:0 1px 2px rgba(0,0,0,.3)}
.nav a{color:var(--white);text-decoration:none;font-family:"Cabin",sans-serif;font-size:11.5px;display:flex;align-items:center;justify-content:center;border-right:1px solid rgba(0,0,0,.2);box-shadow:1px 0 0 rgba(255,255,255,.12)}
.nav a:last-child{border-right:0;box-shadow:none}
.hero{left:59px;top:152px;width:841px;height:261px;border:2px solid #d6d6d6;background:linear-gradient(180deg,#4a7fc1 0%,#8fb4de 40%,#c8b48e 58%,#3c6fae 68%,#1f4f8c 100%)}
.hero-title{left:122px;top:220px;font-family:"Cabin",sans-serif;font-size:25px;color:var(--white);text-shadow:0 1px 3px rgba(0,0,0,.5)}
.dot{top:381px;width:9px;height:9px;border-radius:50%;background:var(--white)}
.dot.off{background:#aaa}
.panel{left:58px;top:421px;width:842px;height:673px;background:var(--white)}
h2{font-family:"Cabin",sans-serif;font-weight:400;color:var(--red);font-size:16px}
.rule{height:0;border-top:1px dotted var(--dots)}
.body-text{font-size:9.4px;line-height:15.7px;color:var(--text);text-align:justify}
.body-text.small{font-size:9px}
.body-text em{color:var(--red)}
.photo{border:1px solid #ddd}
.step{display:flex;align-items:center;gap:6px;top:611px;white-space:nowrap}
.step b{width:42px;height:42px;border-radius:50%;background:var(--red);color:var(--white);font-family:"Cabin",sans-serif;font-weight:400;font-size:19px;display:flex;align-items:center;justify-content:center;flex:none}
.step span{font-family:"Cabin",sans-serif;color:var(--red);font-size:14px}
.more{background:var(--red-dark);color:var(--white);font-size:9.5px;font-weight:600;display:flex;align-items:center;justify-content:center;border-radius:2px;box-shadow:0 1px 2px rgba(0,0,0,.35)}
.avatar{left:652px;top:469px;width:43px;height:43px;border:1px solid #ccc;background:var(--white);padding:3px}
.avatar div{width:100%;height:100%;background:var(--red)}
.quest{left:655px;top:573px;width:230px;height:77px;background:linear-gradient(#f5f5f5,#dcdcdc);border:1px solid #ccc;border-radius:3px}
.quest-icon{left:671px;top:589px;width:45px;height:44px;background:var(--white);border:1px solid #ccc}
.quest-title{left:726px;top:590px;font-family:"Cabin",sans-serif;font-size:12.5px;color:#555}
.quest-link{left:766px;top:614px;font-family:"Cabin",sans-serif;font-style:italic;font-size:16.5px;color:var(--red)}
.story-title{font-size:11.5px;font-weight:600;color:var(--red)}
.form{left:629px;top:702px;width:252px;height:372px;background:var(--red-deep)}
.tab{top:702px;height:31px;font-family:"Cabin",sans-serif;font-size:15px;display:flex;align-items:center;padding-left:7px}
.tab.active{left:629px;width:122px;color:var(--white);background:var(--red-deep)}
.tab.alt{left:751px;width:130px;color:var(--red);background:linear-gradient(#fbe98a,var(--gold));padding-left:15px}
.field-label{left:646px;font-size:10px;color:var(--white)}
.field{left:644px;width:225px;background:var(--white);border:1px solid #e4e4e4}
.check{left:646px;top:996px;font-size:9.5px;color:var(--white);display:flex;align-items:center;gap:7px}
.check i{width:9px;height:9px;background:var(--white);display:block}
.btn{top:1022px;height:22px;background:#5a0608;color:var(--white);font-size:10px;font-weight:600;display:flex;align-items:center;justify-content:center;border-radius:2px}
.foot-links{left:58px;top:1108px;font-size:10.5px;color:#555;word-spacing:1px}
.foot-links span{color:#999;margin:0 4px}
.copy{left:58px;top:1132px;font-size:10.5px;color:#555}
.seal{left:593px;top:1112px;width:66px;height:66px;border-radius:50%;background:radial-gradient(#b08a35,#6b4f14);border:3px solid #8a6b22}
.follow{left:732px;top:1107px;font-family:"Cabin",sans-serif;font-size:12px;color:#666}
.social{top:1135px;width:26px;height:26px;border-radius:50%;background:#b9b9b9}
.assoc{left:813px;top:1112px;width:70px;height:60px;background:#5a86c4}
</style>
</head>
<body>
<div class="abs top-bar"></div>

<div class="abs logo-mark"></div>
<div class="abs logo-name"><span class="l1">LAW OFFICE OF</span><span class="l2">MARTA K. DOLVENIDZE</span></div>

<div class="abs search">Search
  <svg width="10" height="10" viewBox="0 0 10 10"><circle cx="4" cy="4" r="3" fill="none" stroke="#aaa" stroke-width="1.2"/><line x1="6.2" y1="6.2" x2="9" y2="9" stroke="#aaa" stroke-width="1.4"/></svg>
</div>

<div class="abs nav-band"></div>
<nav class="abs nav">
  <a style="width:87px">HOME</a>
  <a style="width:98px">ABOUT US</a>
  <a style="width:94px">LAWYERS</a>
  <a style="width:114px">LATEST NEWS</a>
  <a style="width:131px">LATEST ARTICLES</a>
  <a style="width:130px">PRACTICE AREAS</a>
  <a style="width:111px">CONTACT US</a>
  <a style="width:76px">FAQ</a>
</nav>

<div class="abs hero" role="img" aria-label="Photo of the Golden Gate Bridge and San Francisco bay at dusk"></div>
<div class="abs hero-title">DUIS AUTE IRURE DOLOR</div>
<div class="abs dot off" style="left:83px"></div>
<div class="abs dot" style="left:101px"></div>
<div class="abs dot" style="left:120px"></div>
<div class="abs dot" style="left:139px"></div>

<div class="abs panel"></div>

<h2 class="abs" style="left:76px;top:440px">WELCOME TO COMPLETE BANKRUPTCY INFORMATION</h2>
<div class="abs rule" style="left:76px;top:476px;width:543px"></div>
<p class="abs body-text" style="left:76px;top:494px;width:403px">Sed ut perspiciatis unde omnis iste natus error sit voluptatem accusantium dolor emque laudantium, totam rem aperiam, eaque ipsa quae ab illo invenvoluptatum deleniti atque corrupti quos dolores et quas molestias excepturi sint occaecati cupiditate Sed ut perspiciatis unde omnis iste natus error sit voluptatem accusantium dolor emque laudantium, totam rem aperiam, eaque ipsa quae ab illo invenvoluptatum deleniti atque corrupti quos dolores et quas molestias excepturi sint occaecati cupiditate <em>View more</em></p>
<div class="abs photo" style="left:489px;top:495px;width:136px;height:90px;background:linear-gradient(135deg,#e8dcc4,#9a7a48 60%,#5e4524)" role="img" aria-label="Bronze statue of Lady Justice holding scales"></div>

<div class="abs step" style="left:77px"><b>01</b><span>DEBT RELIEF</span></div>
<div class="abs step" style="left:214px"><b>02</b><span>FORECLOSURE PREVENTION</span></div>
<div class="abs step" style="left:452px"><b>03</b><span>CHAPTER 13</span></div>

<h2 class="abs" style="left:650px;top:442px">MY BLOG</h2>
<div class="abs avatar"><div role="img" aria-label="Author avatar placeholder"></div></div>
<p class="abs body-text small" style="left:709px;top:467px;width:170px">Sed ut perspiciatis unde omnis iste natus error sit voluptatem accusantium dolor emque laudantium, totam rem aperiam, eaque ipsa quae ab illo inven-tore veritatis <em>August 29th, 2012</em></p>
<div class="abs more" style="left:829px;top:546px;width:48px;height:20px">More...</div>

<div class="abs quest"></div>
<svg class="abs" style="left:762px;top:649px" width="24" height="9" viewBox="0 0 24 9"><path d="M0 0 L12 8 L24 0 Z" fill="#dcdcdc"/></svg>
<div class="abs quest-icon"><svg width="45" height="44" viewBox="0 0 45 44"><text x="22" y="29" text-anchor="middle" font-size="20" fill="#ddd" font-family="Cabin, sans-serif">?</text></svg></div>
<div class="abs quest-title">Client Online Questionnaire</div>
<svg class="abs" style="left:743px;top:619px" width="14" height="12" viewBox="0 0 14 12"><path d="M0 0 L7 6 L0 12 Z M6 0 L13 6 L6 12 Z" fill="var(--red)"/></svg>
<div class="abs quest-link">Click here</div>

<div class="abs rule" style="left:76px;top:672px;width:803px"></div>

<h2 class="abs" style="left:76px;top:689px;font-size:15px">Different Types of Bankruptcy and Family Law</h2>
<div class="abs rule" style="left:76px;top:717px;width:543px"></div>

<div class="abs photo" style="left:76px;top:729px;width:190px;height:126px;background:linear-gradient(135deg,#f4ede2,#e4c47a 55%,#f7f2ea)" role="img" aria-label="Happy family with two children smiling together"></div>
<div class="abs story-title" style="left:278px;top:728px">Story TItle line goes here</div>
<p class="abs body-text small" style="left:278px;top:748px;width:304px;text-align:left">Lorem ipsum dolor sit amet, consectetuer adipiscing elit. Nam cursus. Morbi ut mi. Nullam enim leo, egestas id, condimentum at, laoreet mattis, massa.</p>
<p class="abs body-text small" style="left:278px;top:801px;width:304px;text-align:left">Sed eleifend nonummy diam. Praesent mauris ante, elementum et, bibendum at, posuere sit amet, nibh. Duis tincidunt lectus quis dui viverra vestibulum.</p>
<div class="abs more" style="left:522px;top:840px;width:48px;height:20px">More...</div>

<div class="abs photo" style="left:76px;top:904px;width:190px;height:126px;background:linear-gradient(135deg,#5a2a1a,#a0622e 50%,#3b1d12)" role="img" aria-label="Wooden judge's gavel resting on law books"></div>
<div class="abs story-title" style="left:281px;top:908px">Story TItle line goes here</div>
<p class="abs body-text small" style="left:281px;top:926px;width:304px;text-align:left">Lorem ipsum dolor sit amet, consectetuer adipiscing elit. Nam cursus. Morbi ut mi. Nullam enim leo, egestas id, condimentum at, laoreet mattis, massa.</p>
<p class="abs body-text small" style="left:281px;top:980px;width:304px;text-align:left">Sed eleifend nonummy diam. Praesent mauris ante, elementum et, bibendum at, posuere sit amet, nibh. Duis tincidunt lectus quis dui viverra vestibulum.</p>
<div class="abs more" style="left:520px;top:1024px;width:49px;height:21px">More...</div>

<div class="abs form"></div>
<div class="abs tab active">CONTACT FORM</div>
<div class="abs tab alt">CLIENT FORM</div>

<div class="abs field-label" style="top:742px">Name:</div>
<div class="abs field" style="top:759px;height:21px"></div>
<div class="abs field-label" style="top:785px">Email:</div>
<div class="abs field" style="top:801px;height:21px"></div>
<div class="abs field-label" style="top:827px">Phone:</div>
<div class="abs field" style="top:844px;height:21px"></div>
<div class="abs field-label" style="top:868px">Subject:</div>
<div class="abs field" style="top:887px;height:20px"></div>
<div class="abs field-label" style="top:911px">Message:</div>
<div class="abs field" style="top:929px;height:59px"></div>

<div class="abs check"><i></i>Send a copy of this message to yourself</div>
<div class="abs btn" style="left:646px;width:51px">SEND</div>
<div class="abs btn" style="left:708px;width:52px">RESET</div>

<div class="abs foot-links">Home<span>|</span>About us<span>|</span>Lawyers<span>|</span>Latest News<span>|</span>Latest Articles<span>|</span>Practice Areas<span>|</span>Contact us<span>|</span>FAQ</div>
<div class="abs copy">Copyright © 2012 www.dorvanelilaw-example.com &nbsp;&nbsp; All rights reserved.</div>

<div class="abs seal" role="img" aria-label="Certification seal"></div>
<div class="abs follow">FOLLOW US</div>
<div class="abs social" style="left:731px" role="img" aria-label="Social profile link"></div>
<div class="abs social" style="left:768px" role="img" aria-label="Social profile link"></div>
<div class="abs assoc" role="img" aria-label="Professional association membership badge"></div>
</body>
</html>
```